Heritage Hollow Business Cards

Require a business card design. <br/><br/>Needs to include logo (either round or long version) plus these details:<br/>Maya Torvell<br/>Heritage Hollow<br/>maya@kelvadtrading.com.au<br/>02 6481 7395<br/>PO Box Glenwarra NSW 2791<br/>www.heritagehollow.com.au<br/><br/>I need in an editable format so that I can create for multiple staff members. <br/><br/>

Target Market(s)

We are an online store selling renovation products to home owners are builders. Looking for a classic classy design.

Industry/Entity Type

Home And Garden

Contact Information for Business Card

Maya Torvell
Heritage Hollow
maya@kelvadtrading.com.au
02 6481 7395
PO Box Glenwarra NSW 2791
www.heritagehollow.com.au

Colors

Designer to choose colors to be used in the design.

Requirements
Must have
• Must include Logo.

```html
<!DOCTYPE html>
<html lang="en">
<head>
<meta charset="UTF-8">
<title>Heritage Hollow Business Cards</title>
<link href="https://fonts.googleapis.com/css2?family=Josefin+Slab:wght@400;600&display=swap" rel="stylesheet">
<style>
  :root {
    --backdrop: #8e8f8f;
    --card-light: #ffffff;
    --card-dark: #2b2b2b;
    --ink: #1f1f1f;
    --ink-soft: #8a8a8a;
    --ink-mid: #3a3a3a;
    --reverse: #f4f4f4;
  }
  * { margin: 0; padding: 0; box-sizing: border-box; }
  html, body {
    width: 1200px; height: 960px; overflow: hidden;
    background: var(--backdrop);
    font-family: "Josefin Slab", serif;
  }
  .card {
    position: absolute;
    left: 281px;
    width: 655px;
    height: 373px;
  }
  .card--front { top: 59px; background: var(--card-light); }
  .card--back { top: 501px; background: var(--card-dark); }

  .holder { position: absolute; right: 64px; top: 56px; text-align: right; }
  .holder__name {
    font-size: 25px; font-weight: 600; letter-spacing: 0.5px;
    color: var(--ink); line-height: 1;
  }
  .holder__title { font-size: 17px; color: var(--ink-soft); margin-top: 8px; }

  .brand-name {
    position: absolute; left: 73px; top: 150px;
    font-size: 32px; font-weight: 600; color: var(--ink-mid); line-height: 1;
  }

  .details { position: absolute; left: 71px; top: 202px; font-size: 15.5px; line-height: 1; }
  .details__company { color: var(--ink); }
  .details__address { color: var(--ink-soft); margin-top: 10px; }
  .contact-list { list-style: none; margin-top: 14px; }
  .contact-list li {
    display: flex; align-items: center; gap: 8px;
    color: var(--ink-soft); height: 24px;
  }
  .contact-list svg { width: 13px; height: 13px; flex: none; }

  .back-mark {
    position: absolute; left: 221px; top: 52px;
    width: 226px; height: 226px; border-radius: 50%;
    border: 1.5px solid var(--reverse);
    display: flex; align-items: center; justify-content: center;
    text-align: center;
  }
  .back-mark__name {
    font-size: 32px; font-weight: 600; color: var(--reverse); line-height: 1.05;
  }
</style>
</head>
<body>
  <section class="card card--front">
    <div class="holder">
      <div class="holder__name">MAYA TORVELL</div>
      <div class="holder__title">Founder &amp; CEO</div>
    </div>

    <div class="brand-name">Heritage Hollow</div>

    <div class="details">
      <p class="details__company">Heritage Hollow</p>
      <p class="details__address">PO Box Glenwarra NSW 2791</p>
      <ul class="contact-list">
        <li>
          <svg viewBox="0 0 16 16" aria-hidden="true"><path d="M3 1.5l3 3-1.6 1.8c.9 2 2.4 3.5 4.3 4.4L10.5 9l3 3-1.8 2.2C6.5 14 2 9.4 1 4.2z" fill="var(--ink)"/></svg>
          <span>02 6481 7395</span>
        </li>
        <li>
          <svg viewBox="0 0 16 16" aria-hidden="true"><rect x="1" y="3.5" width="14" height="9" fill="var(--ink)"/><path d="M1.5 4l6.5 5 6.5-5" stroke="#fff" stroke-width="1.2" fill="none"/></svg>
          <span>maya@kelvadtrading.com.au</span>
        </li>
        <li>
          <svg viewBox="0 0 16 16" aria-hidden="true" fill="none" stroke="var(--ink)" stroke-width="1.3"><circle cx="8" cy="8" r="6.5"/><ellipse cx="8" cy="8" rx="3" ry="6.5"/><path d="M1.5 8h13M2.5 4.7h11M2.5 11.3h11"/></svg>
          <span>www.heritagehollow.com.au</span>
        </li>
      </ul>
    </div>
  </section>

  <section class="card card--back">
    <div class="back-mark">
      <div class="back-mark__name">Heritage<br>Hollow</div>
    </div>
  </section>
</body>
</html>
```